Building company buisness cards

We are looking for a sharp modern new look for our business cards.
We are a New Zealand based company that specialises in house and land packages.
We have attached a photo of the current logo and would like to see if it can be improved somehow if needed.
We are open to any colours but we have chosen green at this stage.
Feel free to change the font and make the logo smarter looking.
Play with the colours and see what looks best.

We want a card that looks so good know one will want to throw it away!

Target Market(s)

Home buyers

Industry/Entity Type

Building

Contact Information for Business Card

Derek Tolvane
0217394062
dtolvane@quillmarkhomesteads.co.nz
quillmarkhomesteads.co.nz

Font styles to use
Serif
Sans Serif

Colors

Designer to choose colors to be used in the design.

Requirements
Must have
• Logo and company name on one side, details on the other side
Nice to have
• Color codes for the original green are HEX #4a8028, RGB(74,128,40), CMYK(42,0,69,50)
• Round corners, Raised and/or spot UV

```html
<!DOCTYPE html>
<html lang="en">
<head>
<meta charset="utf-8">
<title>Quillmark Homesteads – Business Card</title>
<link href="https://fonts.googleapis.com/css2?family=Open+Sans:wght@400;700&display=swap" rel="stylesheet">
<style>
  :root {
    --page: #e9e6e1;
    --brand-green: #4a8028;
    --card-white: #ffffff;
    --card-dark: #2e2e2e;
    --card-dark-light: #4a4a4a;
    --card-dark-edge: #1c1c1c;
    --text-dark: #333333;
    --text-mid: #555555;
    --rule: #9a9a9a;
  }
  * { box-sizing: border-box; margin: 0; padding: 0; }
  html, body {
    width: 1200px; height: 1021px; overflow: hidden;
    background: var(--page);
    font-family: "Open Sans", Arial, sans-serif;
  }
  .sheet {
    width: 1200px; height: 1021px;
    display: flex; flex-direction: column; align-items: center; justify-content: center;
    gap: 56px;
  }
  .card {
    width: 760px; height: 434px;
    border-radius: 26px;
    position: relative; overflow: hidden;
    box-shadow: 0 6px 18px rgba(0,0,0,0.18);
  }
  /* Logo side */
  .card-back { background: var(--card-dark); }
  .card-back .pattern-area {
    position: absolute; inset: 0;
    background:
      radial-gradient(ellipse at 20% 15%, rgba(255,255,255,0.10) 0%, rgba(255,255,255,0) 55%),
      linear-gradient(135deg, var(--card-dark-light) 0%, #383838 35%, var(--card-dark) 60%, var(--card-dark-edge) 100%);
  }
  .card-back .brand {
    position: absolute; left: 0; right: 0; top: 50%;
    transform: translateY(-50%);
    display: flex; align-items: center; justify-content: center; gap: 16px;
  }
  .brand-dot {
    width: 22px; height: 22px; border-radius: 50%;
    background: var(--brand-green);
    flex: none;
  }
  .brand-name {
    font-weight: 700; font-size: 44px; letter-spacing: 0.5px;
    color: var(--brand-green);
    white-space: nowrap;
  }
  /* Details side */
  .card-front {
    background: linear-gradient(160deg, var(--card-white) 0%, #f3f3f3 100%);
  }
  .front-brand {
    position: absolute; left: 52px; top: 120px; width: 230px;
    display: flex; flex-direction: column; align-items: center; gap: 18px;
  }
  .front-brand .brand-dot { width: 120px; height: 120px; }
  .front-brand .brand-name { font-size: 24px; text-align: center; line-height: 1.2; white-space: normal; }
  .details {
    position: absolute; left: 320px; top: 118px; right: 0;
  }
  .person-name {
    font-weight: 700; font-size: 30px; color: var(--brand-green); line-height: 1.1;
  }
  .person-role {
    font-size: 19px; color: var(--text-mid); margin-top: 2px;
  }
  .divider {
    height: 1.5px; background: var(--rule); margin: 18px 0 20px;
  }
  .contact-list { list-style: none; }
  .contact-list li {
    display: flex; align-items: center; gap: 10px;
    font-size: 19px; color: var(--text-dark); line-height: 1.45;
    white-space: nowrap;
  }
  .contact-list svg { width: 18px; height: 18px; flex: none; }
</style>
</head>
<body>
<main class="sheet">
  <section class="card card-back" aria-label="Card logo side">
    <div class="pattern-area" role="img" aria-label="Repeating embossed brand pattern in dark greys, lighter at the upper left and fading to near black at the lower right"></div>
    <div class="brand">
      <span class="brand-dot"></span>
      <span class="brand-name">quillmark homesteads</span>
    </div>
  </section>

  <section class="card card-front" aria-label="Card details side">
    <div class="front-brand">
      <span class="brand-dot"></span>
      <span class="brand-name">quillmark homesteads</span>
    </div>
    <div class="details">
      <p class="person-name">Derek Tolvane</p>
      <p class="person-role">Founder</p>
      <div class="divider"></div>
      <ul class="contact-list">
        <li>
          <svg viewBox="0 0 24 24" aria-hidden="true"><path fill="#4a8028" d="M6.6 10.8a15.1 15.1 0 0 0 6.6 6.6l2.2-2.2c.3-.3.7-.4 1-.2 1.1.4 2.3.6 3.6.6.6 0 1 .4 1 1V20c0 .6-.4 1-1 1A17 17 0 0 1 3 4c0-.6.4-1 1-1h3.5c.6 0 1 .4 1 1 0 1.3.2 2.5.6 3.6.1.3 0 .7-.2 1z"/></svg>
          0217394062
        </li>
        <li>
          <svg viewBox="0 0 24 24" aria-hidden="true"><rect x="2.5" y="5" width="19" height="14" rx="1" fill="none" stroke="#4a8028" stroke-width="2"/><path d="M3 6l9 7 9-7" fill="none" stroke="#4a8028" stroke-width="2"/></svg>
          dtolvane@quillmarkhomesteads.co.nz
        </li>
        <li>
          <svg viewBox="0 0 24 24" aria-hidden="true"><g fill="none" stroke="#4a8028" stroke-width="1.8"><circle cx="12" cy="12" r="9"/><ellipse cx="12" cy="12" rx="4" ry="9"/><path d="M3 12h18M5 7h14M5 17h14"/></g></svg>
          quillmarkhomesteads.co.nz
        </li>
      </ul>
    </div>
  </section>
</main>
</body>
</html>
```